Breakfast Cafe - The Sunny Nook

It is for my breakfast and lunch cafe with a hawaiian / beach theme. I am open 7 days a week from 7am to 2pm. We serve traditional American food such as omelettes, pancakes, burgers and sandwiches. I'll upload my old card and my new logo to be used. We have a lot of day to day regulars who eat there during the week, our t-shirts actually say 'Locals Only' on them. Hope this helps. Thanks.

Target Market(s)

anyone who has an appetite!

Industry/Entity Type

American Restaurant

Contact Information for Business Card

4815C Marlow Grove Avenue
Long Beach, California
(555) 731-2294

Requirements
Must have
• Address and phone number easily readable.
Nice to have
• beach or tropical theme

```html
<!DOCTYPE html>
<html lang="en">
<head>
<meta charset="utf-8">
<title>The Sunny Nook – Business Card</title>
<link href="https://fonts.googleapis.com/css2?family=Bebas+Neue&family=Parisienne&display=swap" rel="stylesheet">
<style>
  :root {
    --backdrop: #1f1f1f;
    --card: #ffffff;
    --brown: #a8611a;
    --sky: #5bbcd6;
    --ruby: #c8103e;
    --sun: #f4a640;
  }
  html, body {
    margin: 0;
    width: 1200px;
    height: 960px;
    overflow: hidden;
    background: var(--backdrop);
  }
  .card {
    position: absolute;
    left: 300px;
    top: 309px;
    width: 600px;
    height: 343px;
    background: var(--card);
    border-radius: 22px;
    font-family: "Bebas Neue", "Arial Narrow", sans-serif;
  }
  .contact, .about, .motto, .brand { position: absolute; }
  .contact { left: 36px; top: 37px; }
  .address {
    margin: 0;
    font-style: normal;
    color: var(--brown);
    font-size: 23px;
    line-height: 23px;
  }
  .phone {
    margin: 4px 0 0;
    color: var(--sky);
    font-size: 29px;
    line-height: 30px;
  }
  .about { left: 35px; top: 152px; }
  .about p { margin: 0; }
  .kind { color: var(--brown); font-size: 25px; line-height: 26px; }
  .hours { color: var(--sky); font-size: 19px; line-height: 22px; }
  .menu { color: var(--ruby); font-size: 15px; line-height: 18px; }
  .motto {
    left: 36px;
    top: 250px;
    margin: 0;
    font-family: "Parisienne", cursive;
    color: var(--brown);
    font-size: 46px;
    line-height: 64px;
  }
  .brand {
    left: 288px;
    top: 26px;
    width: 282px;
    text-align: center;
  }
  .brand-mark { display: block; margin: 0 auto; }
  .brand-name {
    margin: 6px 0 0;
    color: var(--sky);
    font-size: 50px;
    line-height: 50px;
    font-weight: 400;
  }
  .brand-place {
    margin: 4px 0 0;
    color: var(--brown);
    font-size: 17px;
    letter-spacing: 5px;
  }
</style>
</head>
<body>
  <section class="card">
    <div class="contact">
      <address class="address">4815C Marlow Grove Avenue<br>Long Beach, California</address>
      <p class="phone">P.(555) 731-2294</p>
    </div>
    <div class="about">
      <p class="kind">Breakfast &amp; Lunch Cafe</p>
      <p class="hours">Open 7 days a week from 7am to 2pm.</p>
      <p class="menu">Serving traditional American food</p>
    </div>
    <p class="motto">Locals Only</p>
    <div class="brand">
      <svg class="brand-mark" width="190" height="190" viewBox="0 0 190 190" role="img" aria-label="Round cafe emblem">
        <circle cx="95" cy="95" r="93" fill="var(--sun)"/>
      </svg>
      <h1 class="brand-name">The Sunny Nook</h1>
      <p class="brand-place">Long Beach, CA</p>
    </div>
  </section>
</body>
</html>
```